Marlowe Group needs a business card

I would like the card to be simple but modern and elegant.
I like black and white.
or black and gold.
we are a private finance lender and also are involved in property and property developments.

please look at the business card photos i provided i would like M.G only one one side and all the other details on the other side use fonts that tie in with my theme.

Industry/Entity Type

Finance

Contact Information for Business Card

Marlowe Group (M.G) Daniel Marlowe M: 0413586207 E: danmarl@inboxmail.test

Font styles to use
Other font styles liked:
• Use fonts that would reflect our business

Colors
000000
ffffff

Requirements
Must have
• one side of details
• other side has either M.G or Marlowe Group like in the photos provided

```html
<!DOCTYPE html>
<html lang="en">
<head>
<meta charset="utf-8">
<title>Marlowe Group — Business Card</title>
<link rel="stylesheet" href="https://fonts.googleapis.com/css2?family=Cinzel:wght@400;700&family=Lato:wght@400&display=swap">
<style>
  :root {
    --backdrop: #e9e9e9;
    --card-black: #0b0b0b;
    --gold: #e2b21a;
    --white: #ffffff;
  }
  * { box-sizing: border-box; margin: 0; padding: 0; }
  html, body { width: 1200px; height: 900px; overflow: hidden; }
  body {
    background: var(--backdrop);
    display: flex;
    align-items: center;
    justify-content: center;
    gap: 60px;
  }
  .card {
    position: relative;
    width: 525px;
    height: 300px;
    background: var(--card-black);
    box-shadow: 0 12px 30px rgba(0,0,0,0.18);
  }
  .card-details .holder-name {
    position: absolute;
    top: 34px;
    left: 36px;
    font-family: "Cinzel", serif;
    font-weight: 700;
    font-size: 17px;
    letter-spacing: 1px;
    color: var(--gold);
  }
  .contact-list {
    position: absolute;
    top: 122px;
    left: 36px;
    list-style: none;
    font-family: "Lato", sans-serif;
    font-size: 14px;
    color: var(--white);
  }
  .contact-list li {
    display: flex;
    align-items: center;
    gap: 10px;
    margin-bottom: 10px;
  }
  .contact-icon { width: 12px; height: 12px; flex: none; }
  .brand-block {
    position: absolute;
    right: 40px;
    bottom: 34px;
    text-align: center;
    font-family: "Cinzel", serif;
    font-weight: 400;
    color: var(--gold);
  }
  .brand-initials {
    font-size: 58px;
    line-height: 1;
    letter-spacing: 4px;
  }
  .brand-name {
    margin-top: 8px;
    font-size: 16px;
    letter-spacing: 2px;
  }
  .card-monogram {
    display: flex;
    align-items: center;
    justify-content: center;
  }
  .card-monogram .brand-initials {
    font-family: "Cinzel", serif;
    font-weight: 400;
    color: var(--gold);
    font-size: 92px;
    letter-spacing: 6px;
  }
</style>
</head>
<body>
  <section class="card card-details">
    <h1 class="holder-name">DANIEL MARLOWE</h1>
    <ul class="contact-list">
      <li>
        <svg class="contact-icon" viewBox="0 0 12 12" aria-hidden="true">
          <rect x="3" y="0.5" width="6" height="11" rx="1.2" fill="none" stroke="#e2b21a" stroke-width="1.2"/>
          <line x1="5" y1="9.5" x2="7" y2="9.5" stroke="#e2b21a" stroke-width="1"/>
        </svg>
        <span>0413586207</span>
      </li>
      <li>
        <svg class="contact-icon" viewBox="0 0 12 12" aria-hidden="true">
          <rect x="0.6" y="2" width="10.8" height="8" fill="none" stroke="#e2b21a" stroke-width="1.2"/>
          <polyline points="0.6,2 6,6.5 11.4,2" fill="none" stroke="#e2b21a" stroke-width="1.2"/>
        </svg>
        <span>danmarl@inboxmail.test</span>
      </li>
    </ul>
    <div class="brand-block">
      <div class="brand-initials">M.G</div>
      <div class="brand-name">MARLOWE GROUP</div>
    </div>
  </section>

  <section class="card card-monogram">
    <div class="brand-initials">M.G</div>
  </section>
</body>
</html>
```